Brightwave Reach - Business Card

We need a business card for a Social Media Marketing company that specializes in online marketing for small businesses in Canada using common Social Media platforms such as Pixlora, Chatterly, Blinkpost & Quibber.

I have uploaded a copy of our logo which I would like utilized in the business card. We would like the business card to be modern yet classy design.

Our website is www.brightwavereach.ca

Industry/Entity Type

Marketing

Contact Information for Business Card

Email: info@brightwavereach.ca
Website: www.brightwavereach.ca
Telephone: 604-555-0193

Colors

Designer to choose colors to be used in the design.

Requirements
Must have
• Social Media icons on reverse
• Please add some designs with color.

```html
<!DOCTYPE html>
<html lang="en">
<head>
<meta charset="utf-8">
<title>Brightwave Reach – Business Card</title>
<link rel="stylesheet" href="https://fonts.googleapis.com/css2?family=Open+Sans:wght@400;700;800&display=swap">
<style>
  :root {
    --backdrop: #e9e7e4;
    --card: #121212;
    --card-edge: #1c1c1c;
    --ink: #f2f2f2;
    --ink-soft: #cfcfcf;
    --emboss: #2a2a2a;
    --emboss-line: #3a3a3a;
    --rule: #9a9a9a;
  }
  * { box-sizing: border-box; margin: 0; padding: 0; }
  html, body { width: 1200px; height: 864px; overflow: hidden; }
  body {
    background: var(--backdrop);
    font-family: "Open Sans", Arial, sans-serif;
    display: flex;
    align-items: center;
    justify-content: center;
    gap: 40px;
  }
  .card {
    position: relative;
    width: 540px;
    height: 309px;
    background: var(--card);
    border: 1px solid var(--card-edge);
    box-shadow: 0 10px 24px rgba(0,0,0,.25);
    overflow: hidden;
  }

  /* Reverse side */
  .card-back .brand-emboss {
    position: absolute;
    top: 74px;
    left: 0;
    right: 0;
    display: flex;
    align-items: center;
    justify-content: center;
    gap: 12px;
    color: var(--emboss);
    font-weight: 800;
    font-size: 34px;
    letter-spacing: 1px;
    text-transform: uppercase;
  }
  .brand-emboss .brand-square {
    width: 18px; height: 18px; background: var(--emboss);
  }
  .social-row {
    position: absolute;
    top: 196px;
    left: 40px;
    right: 40px;
    display: flex;
    align-items: center;
    gap: 14px;
  }
  .social-row .rule { flex: 1; height: 1px; background: var(--emboss-line); }
  .social-list { display: flex; gap: 16px; list-style: none; }
  .social-list li {
    display: flex; align-items: center; gap: 6px;
    color: #5a5a5a; font-size: 12px; font-weight: 400;
  }
  .social-list .dot {
    width: 14px; height: 14px; border-radius: 50%;
    border: 1.5px solid #5a5a5a;
  }

  /* Front side */
  .contact {
    position: absolute;
    left: 34px;
    top: 116px;
    color: var(--ink);
  }
  .contact .person { font-weight: 700; font-size: 15px; letter-spacing: .3px; }
  .contact .role {
    font-size: 13px; color: var(--ink-soft); text-transform: uppercase;
    padding-bottom: 5px; border-bottom: 1px solid var(--rule); display: inline-block;
  }
  .contact-list { list-style: none; margin-top: 6px; }
  .contact-list li {
    display: flex; align-items: center; gap: 7px;
    font-size: 12.5px; line-height: 19px; color: var(--ink-soft);
  }
  .contact-list svg { width: 11px; height: 11px; fill: var(--ink); }
  .front-rule {
    position: absolute; left: 34px; right: 34px; top: 236px;
    height: 1px; background: var(--rule);
  }
  .brand-mark {
    position: absolute; right: 34px; top: 96px;
    display: flex; align-items: center; gap: 10px;
    color: var(--ink); font-weight: 800; font-size: 26px;
    text-transform: uppercase; letter-spacing: .5px;
  }
  .brand-mark .brand-square { width: 14px; height: 14px; background: var(--ink); }
</style>
</head>
<body>

  <section class="card card-back" aria-label="Card reverse">
    <div class="brand-emboss"><span class="brand-square"></span>Brightwave Reach</div>
    <div class="social-row">
      <span class="rule"></span>
      <ul class="social-list">
        <li><span class="dot"></span>Chatterly</li>
        <li><span class="dot"></span>Pixlora</li>
        <li><span class="dot"></span>Quibber</li>
      </ul>
      <span class="rule"></span>
    </div>
  </section>

  <section class="card card-front" aria-label="Card front">
    <div class="contact">
      <p class="person">DANA ELLERY</p>
      <p class="role">CEO/Founder</p>
      <ul class="contact-list">
        <li>
          <svg viewBox="0 0 16 16" aria-hidden="true"><path d="M3 1h3l1.5 4-2 1.3a9 9 0 0 0 4.2 4.2L11 8.5l4 1.5v3a2 2 0 0 1-2 2A12 12 0 0 1 1 3a2 2 0 0 1 2-2z"/></svg>
          604-555-0193
        </li>
        <li>
          <svg viewBox="0 0 16 16" aria-hidden="true"><path d="M1 3h14v10H1z M1 3l7 6 7-6" stroke="#121212" stroke-width="1.2"/></svg>
          info@brightwavereach.ca
        </li>
        <li>
          <svg viewBox="0 0 16 16" aria-hidden="true"><path d="M8 0a5.5 5.5 0 0 0-5.5 5.5C2.5 10 8 16 8 16s5.5-6 5.5-10.5A5.5 5.5 0 0 0 8 0zm0 8a2.5 2.5 0 1 1 0-5 2.5 2.5 0 0 1 0 5z"/></svg>
          www.brightwavereach.ca
        </li>
      </ul>
    </div>
    <div class="front-rule"></div>
    <div class="brand-mark"><span class="brand-square"></span>Brightwave Reach</div>
  </section>

</body>
</html>
```